Design for Torvik Ginger Chewy Candy!

Hello! We are Torvik Enterprises Corp, a food manufacturer and distributor based in Los Angeles, CA. We manufacture Chips, Cookies, Juices, Dairy, and last but not least, Candies! We are launching our Ginger Chewy Candy soon and we need a great design for it!

Our Ginger Chewy Candy is a perfect mixture between sweet and spicy from the ginger itself. Torvik Ginger Chewy Candy a good relief for sore throat and nausea.

Now, other than a great design, we also welcome brand suggestions for the candy.
If you can come up with a logo for the Ginger Candy, that would be swell!

We are open to unique and out of the box design. We chose a few color schemes for the design, but feel free to step out of the box if you feel it suits the brand.

We don't have the exact size for the plastic pouch, but it should be a generic small plastic pouch size (approximately 4 oz resealable plastic pouch)

Please have fun designing the project, we can't wait to see all the great designs!

Cheers!

Target Market(s)

USA and Asian market
Age 30-70
Male and Female

Industry/Entity Type

Manufacture

Font styles to use
Serif
Sans Serif
Decorative

Colors
fff3d1
fee18a
fece3e
fbc994
fce8d3

Requirements
Must have
• Torvik Logo
• A picture of ginger (illustrations or photographs are welcome)
Nice to have
• Coating suggestions like Matte surface or SPOT UV
• Give us ideas of what the name of the chewy candy should be. Product name ideas are welcome!

```html
<!DOCTYPE html>
<html lang="en">
<head>
<meta charset="utf-8">
<title>Torvik Ginger Candy – Pouch Front</title>
<link href="https://fonts.googleapis.com/css2?family=Lobster&family=Nunito:wght@600;700&display=swap" rel="stylesheet">
<style>
  :root {
    --stage: #ffffff;
    --cream: #f9e4ad;
    --honey: #f6b63f;
    --amber: #f3a51f;
    --butter: #f2d57f;
    --white: #ffffff;
    --mist: #dfe8f2;
    --navy: #2b3a8e;
    --leaf: #3aa14a;
    --teal: #1e6b57;
    --sky: #3f7fc0;
    --ginger-skin: #e9c9a6;
    --ginger-flesh: #f4d54c;
  }
  * { margin: 0; padding: 0; box-sizing: border-box; }
  html, body {
    width: 960px; height: 1200px; overflow: hidden;
    background: var(--stage);
  }
  .canvas { position: relative; width: 960px; height: 1200px; }
  .pouch-front {
    position: absolute; left: 190px; top: 205px;
    width: 580px; height: 830px; overflow: hidden;
  }
  .pouch-front .backdrop { position: absolute; inset: 0; width: 100%; height: 100%; }
  .ginger-art {
    position: absolute; left: 65px; top: 265px;
    width: 325px; height: 225px;
    border-radius: 48% 52% 46% 54% / 50% 50% 50% 50%;
    background: radial-gradient(ellipse at 55% 60%, var(--ginger-flesh) 0%, var(--ginger-skin) 60%, rgba(233,201,166,0.6) 100%);
  }
  .brand {
    position: absolute; left: 358px; top: 196px;
    display: flex; align-items: center; gap: 8px;
    font-family: "Nunito", sans-serif; font-weight: 700;
    font-size: 46px; line-height: 1; color: var(--navy); letter-spacing: -0.5px;
  }
  .brand-dot { width: 11px; height: 11px; border-radius: 50%; background: var(--leaf); }
  .claim {
    position: absolute; left: 330px; top: 338px;
    font-family: "Nunito", sans-serif; font-weight: 600;
    font-size: 15px; line-height: 24px; color: var(--teal);
  }
  .claim span { display: block; }
  .claim span + span { padding-left: 13px; }
  .product-name { font-family: "Lobster", cursive; font-weight: 400; line-height: 1; }
  .product-name .word {
    position: absolute; white-space: nowrap;
    transform: rotate(-8deg); transform-origin: center;
  }
  .product-name .word-ginger { left: 130px; top: 498px; font-size: 115px; color: var(--amber); }
  .product-name .word-candy { left: 238px; top: 612px; font-size: 100px; color: var(--butter); }
  .net-weight {
    position: absolute; left: 150px; top: 710px;
    font-family: "Nunito", sans-serif; font-weight: 600;
    font-size: 19px; color: var(--sky);
  }
</style>
</head>
<body>
<div class="canvas">
  <section class="pouch-front">
    <svg class="backdrop" viewBox="0 0 580 830" preserveAspectRatio="none" aria-hidden="true">
      <defs>
        <linearGradient id="warmBase" x1="0" y1="0" x2="0" y2="1">
          <stop offset="0" stop-color="var(--cream)"/>
          <stop offset="0.45" stop-color="#f8d58a"/>
          <stop offset="0.65" stop-color="var(--honey)"/>
          <stop offset="1" stop-color="#f7c869"/>
        </linearGradient>
        <linearGradient id="lowerWhite" x1="0" y1="0" x2="0" y2="1">
          <stop offset="0.55" stop-color="var(--white)"/>
          <stop offset="1" stop-color="var(--mist)"/>
        </linearGradient>
      </defs>
      <rect class="base" width="580" height="830" fill="url(#warmBase)"/>
      <path class="swoosh-edge" d="M200,0 C322,30 316,100 316,170 C316,270 352,314 422,309 C486,304 540,276 580,252" fill="none" stroke="var(--amber)" stroke-width="7"/>
      <path class="swoosh-top" d="M225,0 C335,35 328,100 328,170 C328,262 362,300 422,295 C482,290 540,262 580,236 L580,0 Z" fill="var(--white)"/>
      <path class="band-pale" d="M40,830 L40,720 C60,610 190,572 320,505 C430,448 535,360 580,262 L580,830 Z" fill="var(--butter)"/>
      <path class="swoosh-bottom" d="M62,830 L62,728 C82,628 205,590 335,523 C445,466 545,380 580,290 L580,830 Z" fill="url(#lowerWhite)"/>
    </svg>

    <div class="ginger-art" role="img" aria-label="Illustration of a fresh ginger root with green leaves and sliced ginger pieces"></div>

    <div class="brand"><span class="brand-name">Torvik</span><span class="brand-dot"></span></div>

    <p class="claim"><span>a good relief for sore</span><span>throat and nausea.</span></p>

    <h1 class="product-name">
      <span class="word word-ginger">Ginger</span>
      <span class="word word-candy">Candy</span>
    </h1>

    <p class="net-weight">4oz</p>
  </section>
</div>
</body>
</html>
```